Business Card For Halvenmoor Financial Consulting

Hi, I would like a business card designed. Bold, modern.
Please use the same design as the logo. I have also attached the website design to see the overall theme.
Wordmark Font
Color: Hex: #01AEF7

```html
<!DOCTYPE html>
<html lang="en">
<head>
<meta charset="utf-8">
<title>Halvenmoor Financial Consulting — Business Card</title>
<link href="https://fonts.googleapis.com/css2?family=Montserrat:wght@400;500;700&display=swap" rel="stylesheet">
<style>
  :root{
    --stage:#3b3b3b;
    --card:#1a2530;
    --card-deep:#141d26;
    --accent:#01aef7;
    --ink:#ffffff;
    --muted:#c9d3db;
  }
  *{margin:0;padding:0;box-sizing:border-box}
  html,body{width:1200px;height:801px;overflow:hidden}
  body{
    background:var(--stage);
    font-family:"Montserrat",Arial,sans-serif;
    position:relative;
  }
  .card{
    position:absolute;
    top:240px;
    width:560px;height:320px;
    background:var(--card);
    border-bottom:3px solid var(--accent);
    overflow:hidden;
  }
  .card--front{left:30px}
  .card--back{left:610px}

  /* front */
  .brand{
    position:absolute;left:34px;top:70px;
    display:flex;align-items:center;gap:12px;
  }
  .brand__mark{
    width:30px;height:30px;border:3px solid var(--accent);
  }
  .brand__name{
    font-weight:700;font-size:27px;letter-spacing:1px;color:var(--ink);line-height:1;
  }
  .brand__sub{
    display:block;font-weight:700;font-size:8.5px;letter-spacing:6.2px;color:var(--ink);margin-top:6px;
  }
  .person{
    position:absolute;right:34px;top:44px;text-align:right;
  }
  .person__name{font-weight:700;font-size:21px;color:var(--accent);letter-spacing:-.3px}
  .person__role{font-size:13px;color:var(--ink);margin-top:2px}
  .divider{
    position:absolute;left:210px;right:28px;top:130px;height:1px;background:var(--accent);
  }
  .address{
    position:absolute;right:34px;top:148px;text-align:right;
    font-size:14px;line-height:1.35;color:var(--ink);
  }
  .contacts{
    position:absolute;left:34px;bottom:34px;list-style:none;
    font-size:14px;line-height:1.4;color:var(--ink);
  }
  .contacts li{display:flex;align-items:center;gap:9px}
  .contacts svg{width:11px;height:11px;flex:none}

  /* back */
  .back__pattern{
    position:absolute;inset:0;
    background:linear-gradient(135deg,#22313e 0%,#1a2530 45%,var(--card-deep) 100%);
  }
  .back__mark{
    position:absolute;right:110px;top:118px;
    width:70px;height:70px;border:5px solid var(--accent);
  }
</style>
</head>
<body>

<section class="card card--front" aria-label="Business card front">
  <div class="brand">
    <span class="brand__mark" aria-hidden="true"></span>
    <div class="brand__name">HALVENMOOR
      <span class="brand__sub">FINANCIAL CONSULTING</span>
    </div>
  </div>

  <div class="person">
    <p class="person__name">MARLO VENTHE</p>
    <p class="person__role">President</p>
  </div>

  <div class="divider"></div>

  <address class="address" style="font-style:normal">
    1180 Cove Ridge Harbor<br>Port Adley CA 90412
  </address>

  <ul class="contacts">
    <li>
      <svg viewBox="0 0 12 12" aria-hidden="true"><path d="M2.5 1h2l1 2.6-1.3.9a6 6 0 0 0 3.3 3.3l.9-1.3 2.6 1v2A1.5 1.5 0 0 1 9.5 11 8.5 8.5 0 0 1 1 2.5 1.5 1.5 0 0 1 2.5 1z" fill="#01aef7"/></svg>
      555-014-2290
    </li>
    <li>
      <svg viewBox="0 0 12 12" aria-hidden="true"><rect x="1" y="2.5" width="10" height="7" rx="1" fill="#01aef7"/><path d="M1.5 3l4.5 3.5L10.5 3" stroke="#1a2530" fill="none" stroke-width="1"/></svg>
      info@HalvenmoorConsulting.com
    </li>
    <li>
      <svg viewBox="0 0 12 12" aria-hidden="true"><circle cx="6" cy="6" r="5" fill="#01aef7"/><path d="M1 6h10M6 1c-2.5 3-2.5 7 0 10M6 1c2.5 3 2.5 7 0 10" stroke="#1a2530" fill="none" stroke-width=".8"/></svg>
      www.HalvenmoorConsulting.com
    </li>
  </ul>
</section>

<section class="card card--back" aria-label="Business card back">
  <div class="back__pattern" role="img" aria-label="Embossed repeating brand pattern in dark navy tones"></div>
  <span class="back__mark" aria-hidden="true"></span>
</section>

</body>
</html>
```